Website Home Page for Women's Health Medical Office

Redesign existing homepage for website using existing logo. Current website location is www.meadowcrestwomens.com. Please give it a modern, streamlined, playful feel.

Please give it a feminine feel and make it bright and cheerful using logo colors.

Target Market(s)

Women between the ages of 25-45

Industry/Entity Type

Medical Office

Coding

Coded - Design and coding required

Number of Pages Required

1 page

Font styles to use
Sans Serif
Other font styles liked:
• SEGOI UI script for text and GIL SANS for bold (or their equivilent)

Colors
E54698
E96AAD
F1A4CE
F9D9EA
FCEFF6

Requirements
Must have
• Existing logo. Logo Colors. Feminine, cheerful, simple design. all relevant contact information
Nice to have
• clean lines and streamlined look
Should not have
• Cluttered

```html
<!DOCTYPE html>
<html lang="en">
<head>
<meta charset="utf-8">
<title>Meadowcrest OB/GYN</title>
<link href="https://fonts.googleapis.com/css2?family=Roboto:wght@400;500;700;900&family=Arimo:wght@400;700&display=swap" rel="stylesheet">
<style>
:root{
  --pink:#f0509c;
  --pink-mid:#e96aad;
  --pink-soft:#f1a4ce;
  --pink-band:#f7cbe1;
  --pink-pale:#fcecf5;
  --ink:#222;
  --body:#555;
  --footer:#2b2b2b;
  --white:#fff;
}
*{box-sizing:border-box;margin:0;padding:0}
html,body{width:1200px;height:3298px;overflow:hidden}
body{position:relative;background:var(--white);font-family:"Arimo",Arial,sans-serif;color:var(--body)}
.abs{position:absolute}
.topbar{left:512px;top:0;width:688px;height:51px;background:var(--pink);clip-path:polygon(0 0,100% 0,100% 100%,52px 100%);color:#fff;font-size:15px}
.topbar span{position:absolute;top:16px;display:flex;align-items:center;gap:6px}
.brand{left:115px;top:72px;font-family:"Roboto",sans-serif;font-weight:700;font-size:19px;color:var(--ink);display:flex;align-items:center;gap:8px}
.brand i{width:14px;height:14px;border-radius:50%;background:var(--pink);display:block}
.nav a{position:absolute;top:87px;font-family:"Roboto",sans-serif;font-size:16px;color:#333;text-decoration:none}
.nav a.active{color:var(--pink);border-bottom:2px solid var(--pink-soft);padding-bottom:4px}
.hero{left:0;top:130px;width:1200px;height:642px;background:linear-gradient(90deg,#eef0f2 0%,#e3e4e6 45%,#d2c6bd 70%,#b8aaa0 100%)}
.hero h1{position:absolute;left:111px;top:204px;font-family:"Roboto",sans-serif;font-weight:700;font-size:51px;color:var(--pink)}
.hero p{position:absolute;left:112px;top:266px;width:460px;font-size:14px;line-height:29px;color:#333}
.btn{position:absolute;width:211px;height:59px;background:var(--pink);color:#fff;font-family:"Roboto",sans-serif;font-weight:700;font-size:15px;display:flex;align-items:center;justify-content:center;box-shadow:0 6px 12px rgba(0,0,0,.18)}
.dots{left:560px;display:flex;gap:5px}
.dots i{width:13px;height:13px;border:2px solid #fff;border-radius:50%;display:block}
.dots i:first-child{background:radial-gradient(#fff 35%,transparent 40%)}
.photo{background:linear-gradient(160deg,#5b6478,#3a3f52 60%,#2b2f3f)}
.photo.warm{background:linear-gradient(160deg,#c7b49a,#8fb1c9 50%,#d9a9a2)}
.h2{font-family:"Roboto",sans-serif;font-weight:700;font-size:33px;color:var(--pink);line-height:43px}
.h3{font-family:"Roboto",sans-serif;font-weight:700;font-size:26px;color:var(--ink);line-height:39px}
.copy{font-size:13.5px;line-height:26px;color:var(--body)}
.copy p{margin-bottom:10px}
.copy b{color:var(--pink)}
.band{left:0;top:1998px;width:1200px;height:257px;background:var(--pink-band);text-align:center;font-family:"Roboto",sans-serif}
.band .kicker{margin-top:62px;font-size:22px;color:var(--pink)}
.band h2{margin-top:12px;font-size:40px;font-weight:900;color:var(--ink)}
.band .cta{margin-top:14px;font-size:18px;color:var(--ink)}
.band .cta u{color:var(--pink)}
.help{left:0;top:2320px;width:1200px;text-align:center;font-family:"Roboto",sans-serif}
.help h2{font-size:41px;font-weight:900;color:var(--ink)}
.help .sub{margin-top:14px;font-size:18px;color:#444}
.svc{position:absolute;top:2440px;width:230px;text-align:center}
.svc .ic{width:92px;height:92px;border-radius:50%;background:var(--pink-band);margin:0 auto;display:flex;align-items:center;justify-content:center}
.svc h4{margin-top:23px;font-family:"Roboto",sans-serif;font-weight:500;font-size:15px;color:var(--ink)}
.svc p{margin-top:8px;font-size:12.5px;line-height:24px;color:#666}
.svc .go{margin:10px auto 0;width:16px;height:16px;border-radius:50%;background:var(--pink);display:flex;align-items:center;justify-content:center}
.footer{left:0;top:2758px;width:1200px;height:540px;background:var(--footer);color:#eee;font-size:14px}
.fnav{position:absolute;top:44px;left:0;width:1200px;display:flex;justify-content:center;gap:47px;font-size:15px}
.rule{position:absolute;left:111px;width:978px;height:1px;background:#888}
.col{position:absolute;top:127px;line-height:32.6px;list-style:none}
.copyr{position:absolute;top:490px;width:1200px;text-align:center;font-size:13px}
</style>
</head>
<body>
<header>
  <div class="abs topbar">
    <span style="left:80px"><svg width="12" height="12" viewBox="0 0 24 24"><path fill="#fff" d="M6.6 10.8a15 15 0 006.6 6.6l2.2-2.2c.3-.3.7-.4 1-.2 1.1.4 2.3.6 3.6.6.6 0 1 .4 1 1V20c0 .6-.4 1-1 1A17 17 0 013 4c0-.6.4-1 1-1h3.5c.6 0 1 .4 1 1 0 1.3.2 2.5.6 3.6.1.3 0 .7-.2 1z"/></svg>(555) 240-1180</span>
    <span style="left:226px"><svg width="12" height="12" viewBox="0 0 24 24"><path fill="#fff" d="M6.6 10.8a15 15 0 006.6 6.6l2.2-2.2c.3-.3.7-.4 1-.2 1.1.4 2.3.6 3.6.6.6 0 1 .4 1 1V20c0 .6-.4 1-1 1A17 17 0 013 4c0-.6.4-1 1-1h3.5c.6 0 1 .4 1 1 0 1.3.2 2.5.6 3.6.1.3 0 .7-.2 1z"/></svg>555-240-1193</span>
    <span style="left:372px"><svg width="15" height="11" viewBox="0 0 24 18"><rect width="24" height="18" rx="2" fill="#fff"/><path d="M1 1l11 9 11-9" stroke="#f0509c" stroke-width="2" fill="none"/></svg>hello@meadowcrestwomens.com</span>
  </div>
  <div class="abs brand"><i></i>Meadowcrest OB/GYN</div>
  <nav class="nav">
    <a class="active" style="left:621px">Home</a>
    <a style="left:700px">Services</a>
    <a style="left:797px">Resources</a>
    <a style="left:909px">About Us</a>
    <a style="left:1011px">Contact Us</a>
  </nav>
</header>

<section class="abs hero" role="img" aria-label="Expectant mother sitting cross-legged on a bright bed, smiling toward a window">
  <h1>MEADOWCREST OB GYN</h1>
  <p>At Meadowcrest OB/GYN in Willow Bend, California, we believe better health starts when the patient is educated. For this reason, we take time to listen to our patients concerns, explain each option available,</p>
  <div class="btn" style="left:111px;top:369px">GET STARTED</div>
  <div class="abs dots" style="top:594px"><i></i><i></i><i></i><i></i><i></i></div>
</section>

<section>
  <div class="abs photo" style="left:111px;top:855px;width:446px;height:520px" role="img" aria-label="Portrait of a smiling physician in navy scrubs with arms crossed"></div>
  <h2 class="abs h2" style="left:599px;top:900px;width:480px">WELCOME TO MEADOWCREST OB/GYN, WILLOW BEND, CA</h2>
  <h3 class="abs h3" style="left:599px;top:996px;width:480px">SERVING WILLOW BEND MEDICAL CENTER</h3>
  <div class="abs copy" style="left:599px;top:1088px;width:490px"><p>At Meadowcrest OB/GYN in Willow Bend, California, we believe better health starts when the patient is educated. For this reason, we take time to listen to our patients concerns, explain each option available, and to answer any questions our patients may have so that they can make informed decisions. At Meadowcrest OB/GYN, our providers tailor every procedure performed and treatment option recommended to meet the specific needs of our patients.</p></div>
  <div class="btn" style="left:599px;top:1261px">READ MORE</div>
</section>

<section>
  <h2 class="abs h2" style="left:111px;top:1486px">YOUR OB/GYN SPECIALISTS</h2>
  <div class="abs copy" style="left:111px;top:1538px;width:490px">
    <p>Meadowcrest OB/GYN offers you the best care possible in a personalized setting. We are currently accepting patients. Call our office now to make an appointment.</p>
    <p>Meadowcrest OB/GYN (located near Willow Bend Hospital in Willow Bend, CA) is a medical office that specializes in Christ-centered healthcare for women of all ages. <b>Our team of exclusively female providers</b> have years of experience taking care of women with a variety of pregnancy and gynecology concerns.</p>
    <p>Whether you need a routine examination, help during your pregnancy, have questions on birth control, or another female concern, we offer the best care possible for our patients. That is why better health starts here.</p>
  </div>
  <div class="btn" style="left:111px;top:1806px">READ MORE</div>
  <div class="abs photo warm" style="left:643px;top:1421px;width:445px;height:519px" role="img" aria-label="Nurse in blue scrubs holding a newborn baby in a hospital room"></div>
</section>

<section class="abs band">
  <div class="kicker">Better Health Starts Here!</div>
  <h2>NOW ACCEPTING NEW PATIENTS</h2>
  <div class="cta"><u>Click Here</u> for an Appointment &nbsp; (or) &nbsp; Call Us At (555) 240-1180</div>
</section>

<section class="abs help">
  <h2>HOW CAN WE HELP YOU?</h2>
  <div class="sub">Health Services Offered</div>
</section>
<div class="svc" style="left:108px">
  <div class="ic"><svg width="44" height="50" viewBox="0 0 44 50" fill="none" stroke="#f0509c" stroke-width="2"><circle cx="22" cy="8" r="6"/><path d="M14 18c-4 8-4 18 2 28h14c6-6 8-16 0-22"/><path d="M22 32l-3-3a2 2 0 013-3 2 2 0 013 3z"/></svg></div>
  <h4>PREGNANCY CARE</h4>
  <p>Receiving regular care in pregnancy is important for the health of both you and your baby. Our obstetricians work with you every step of the way</p>
  <div class="go"><svg width="8" height="8" viewBox="0 0 8 8"><path d="M3 1l3 3-3 3" stroke="#fff" stroke-width="1.6" fill="none"/></svg></div>
</div>
<div class="svc" style="left:358px">
  <div class="ic"><svg width="44" height="50" viewBox="0 0 44 50" fill="none" stroke="#f0509c" stroke-width="2"><circle cx="22" cy="14" r="9"/><path d="M10 46c0-14 4-20 12-20s12 6 12 20z"/><path d="M14 36h16"/></svg></div>
  <h4>BIRTH CONTROL</h4>
  <p>Our gynecologists are knowledgeable on all forms of birth control including the IUD, arm implant, vaginal ringinsertion, birth control pills, and more!</p>
  <div class="go"><svg width="8" height="8" viewBox="0 0 8 8"><path d="M3 1l3 3-3 3" stroke="#fff" stroke-width="1.6" fill="none"/></svg></div>
</div>
<div class="svc" style="left:609px">
  <div class="ic"><svg width="44" height="50" viewBox="0 0 44 50" fill="none" stroke="#f0509c" stroke-width="2"><path d="M10 26c0-14 4-20 12-20s12 6 12 20"/><path d="M6 46c2-8 8-12 16-12s14 4 16 12"/><path d="M14 22c4 0 10-4 12-8"/></svg></div>
  <h4>WELL WOMAN EXAMS</h4>
  <p>Our providers will help you to stay healthy by performing a physical exam on you annually. We will screen you for multiple health conditions</p>
  <div class="go"><svg width="8" height="8" viewBox="0 0 8 8"><path d="M3 1l3 3-3 3" stroke="#fff" stroke-width="1.6" fill="none"/></svg></div>
</div>
<div class="svc" style="left:859px">
  <div class="ic"><svg width="44" height="50" viewBox="0 0 44 50" fill="none" stroke="#f0509c" stroke-width="2"><path d="M14 6v12c0 6 4 8 4 14v14"/><path d="M30 6v10c0 5-4 7-4 12v18"/><circle cx="26" cy="32" r="7"/></svg></div>
  <h4>WOMEN'S HEALTH</h4>
  <p>Whether you are dealing with painful or irregular periods, fibroids, or other women's health issues, we can help. We offer a variety of the most up-to-date</p>
  <div class="go"><svg width="8" height="8" viewBox="0 0 8 8"><path d="M3 1l3 3-3 3" stroke="#fff" stroke-width="1.6" fill="none"/></svg></div>
</div>

<footer class="abs footer">
  <nav class="fnav"><span>Home</span><span>About Us</span><span>News</span><span>Patient Resources</span><span>Privacy Policy</span><span>Contact Us</span></nav>
  <div class="rule" style="top:93px"></div>
  <ul class="col" style="left:223px"><li>Meridell Plan</li><li>Valley Plan Direct</li><li>Harborcare of Linden</li><li>Harborcare of Ashby</li><li>SENIORLINK</li><li>Bright Cove Linden</li><li>Service Plan Prime</li><li>Orchard Physicians</li><li>Brightpath Open Access Select</li><li>Summit Select</li></ul>
  <ul class="col" style="left:436px"><li>Summit Select</li><li>Clearwater Shield</li><li>Cedarline Plan</li><li>Cedarline Local Plus</li><li>Veteran Care Plan</li><li>ELMS</li><li>FEHP</li><li>CareGrid</li><li>Hollis Plan</li></ul>
  <ul class="col" style="left:591px"><li>Steel Trades Trust Fund</li><li>Builders Health &amp; Welfare Fund</li><li>Postal Carriers</li><li>Equipment Engineers</li><li>Metal Trades Workers</li><li>Service Plan Select</li><li>UnionWell Healthcare</li><li>UFSW</li><li>UBR</li></ul>
  <ul class="col" style="left:840px"><li>Harborcare of Sunridge</li></ul>
  <div class="rule" style="top:462px"></div>
  <div class="copyr">© 2022 All Rights Reserved</div>
</footer>
</body>
</html>
```